Looking to build a senior life alert web page

We definitely want to incorporate pictures of the product in which we're selling and want colors that resonate with the senior community. We're looking for something also clean and very easy to navigate. We're looking to pick a design immediately!
Based on something similar to that of our competition which can be located at the following
https://www.tovrelcarelink.example/
https://www.wellkestrix.example/

attached is the product we're selling

The name of our company is the golden harbor circle

Target Market(s)

Elderly people looking for a life alert device

Industry/Entity Type

Medical Equipment

Number of Pages Required

3 page

Font styles to use
Serif

Colors

Designer to choose colors to be used in the design.

Requirements
Must have
• Pictures of the product a nice UI experience that can be easily made mobile friendly
Nice to have
• Including area for video content maybe / friendly color LOGOS are attached for our company

```html
<!DOCTYPE html>
<html lang="en">
<head>
<meta charset="utf-8">
<title>Golden Harbor Circle</title>
<link rel="stylesheet" href="https://fonts.googleapis.com/css2?family=PT+Serif:wght@400;700&family=Open+Sans:wght@400;600&display=swap">
<style>
:root{
  --teal:#1f8784;
  --teal-dark:#176b69;
  --orange:#e0592f;
  --orange-deep:#d9552c;
  --ink:#222;
  --muted:#666;
  --light:#f2f2f2;
  --footer:#ececec;
  --white:#fff;
}
*{box-sizing:border-box;margin:0;padding:0}
html,body{width:1200px;height:3147px;overflow:hidden;background:var(--white)}
body{position:relative;font-family:"Open Sans",Arial,sans-serif;color:var(--ink)}

/* header */
.site-header{position:absolute;left:0;top:0;width:1200px;height:71px;background:var(--white);z-index:3}
.brand-badge{position:absolute;left:80px;top:0;width:216px;height:120px;background:var(--white);border-radius:0 0 108px 108px/0 0 60px 60px;display:flex;flex-direction:column;align-items:center;justify-content:center;gap:6px;z-index:4}
.brand-dot{width:44px;height:44px;border-radius:50%;background:var(--orange)}
.brand-name{font-family:"PT Serif",Georgia,serif;font-size:17px;color:var(--ink);font-weight:700;letter-spacing:.3px}
.main-nav{position:absolute;left:306px;top:24px;display:flex;gap:30px;font-family:"PT Serif",Georgia,serif;font-size:15px}
.main-nav a{color:var(--ink);text-decoration:none}
.main-nav a.active{color:var(--orange)}
.header-icons{position:absolute;left:980px;top:20px;display:flex;gap:12px}
.header-icons span{width:30px;height:30px;border-radius:50%;background:var(--orange);display:flex;align-items:center;justify-content:center}

/* hero */
.hero{position:absolute;left:0;top:71px;width:1200px;height:479px;background:linear-gradient(100deg,#d9e4ea 0%,#b7ccd8 45%,#8fa8b5 75%,#a4aa90 100%)}
.hero-frame{position:absolute;left:134px;top:118px;width:655px;height:283px;border:4px solid var(--orange);border-right-color:var(--teal);border-top-color:var(--teal)}
.hero h1{position:absolute;left:174px;top:152px;font-family:"PT Serif",Georgia,serif;font-weight:400;font-size:34px;color:#2a2a2a;letter-spacing:.5px}
.hero p{position:absolute;left:174px;top:202px;width:430px;font-family:"PT Serif",Georgia,serif;font-size:18px;line-height:1.4;color:#333}
.btn{display:inline-flex;align-items:center;justify-content:center;background:var(--teal);color:var(--white);font-family:"PT Serif",Georgia,serif;border-radius:24px;border:3px solid #cfe3e2}
.hero .btn{position:absolute;left:174px;top:303px;width:166px;height:48px;font-size:16px}
.hero-arrows{position:absolute;left:1070px;top:405px;display:flex;gap:10px}
.hero-arrows span{width:38px;height:38px;border-radius:50%;background:var(--orange);display:flex;align-items:center;justify-content:center}

/* welcome */
.welcome-title{position:absolute;left:0;width:1200px;top:620px;text-align:center;font-family:"PT Serif",Georgia,serif;font-size:32px;font-weight:400}
.welcome-text{position:absolute;left:240px;width:720px;top:674px;text-align:center;font-size:13.5px;line-height:1.7;color:var(--muted)}
.feature{position:absolute;text-align:center;font-family:"PT Serif",Georgia,serif;font-size:19px}
.feature-center{position:absolute;left:487px;top:789px;width:231px;height:231px;border-radius:50%;background:var(--teal);color:var(--white);text-align:center;padding-top:26px}
.feature-center h3{font-family:"PT Serif",Georgia,serif;font-weight:400;font-size:19px;margin-top:10px}
.feature-center p{font-size:12px;line-height:1.75;width:176px;margin:6px auto 0}

/* mission */
.mission{position:absolute;left:0;top:1106px;width:1200px;height:400px;background:linear-gradient(90deg,#4b3b2c 0%,#6b5a3c 40%,#3a4a33 75%,#2c3528 100%)}
.mission-art{position:absolute;left:42px;top:24px;width:409px;height:376px;background:linear-gradient(180deg,#b9a6c9,#6f84b8);border-radius:6px}
.mission h2{position:absolute;left:564px;top:60px;font-family:"PT Serif",Georgia,serif;font-weight:400;font-size:30px;color:var(--white)}
.mission p{position:absolute;left:564px;top:110px;width:480px;font-size:14px;line-height:1.75;color:#eee}
.mission .btn{position:absolute;left:564px;top:264px;width:164px;height:48px;font-size:16px}

/* pricing */
.pricing-title{position:absolute;left:0;width:1200px;top:1592px;text-align:center;font-family:"PT Serif",Georgia,serif;font-size:31px;font-weight:400}
.product-frame{position:absolute;left:69px;top:1695px;width:218px;height:239px;border:2px solid var(--orange);padding:18px}
.product-shot{width:100%;height:100%;background:linear-gradient(180deg,#f3f3f3,#d9d9d9);border-radius:6px}
.product-pointer{position:absolute;left:288px;top:1802px}
.plan{position:absolute;top:1664px;width:216px;height:304px;background:var(--teal);border-radius:12px;color:var(--white);text-align:center}
.plan h4{font-family:"PT Serif",Georgia,serif;font-weight:400;font-size:13px;margin-top:18px;letter-spacing:.5px}
.plan .price{font-family:"PT Serif",Georgia,serif;font-weight:700;font-size:25px;margin-top:8px}
.plan .price small{font-size:11px;font-weight:400}
.plan ul{list-style:none;background:var(--light);color:#444;text-align:left;margin-top:14px;height:168px;padding:18px 0 0 30px;border-radius:10px 10px 12px 12px;font-family:"PT Serif",Georgia,serif;font-size:11.5px}
.plan li{height:25px;display:flex;align-items:center;gap:8px}
.plan .order{font-family:"PT Serif",Georgia,serif;font-size:17px;margin-top:20px}

/* video band */
.video-band{position:absolute;left:0;top:2079px;width:1200px;height:445px;background:var(--orange-deep)}
.video-panel{position:absolute;left:451px;top:36px;width:646px;height:371px;background:linear-gradient(180deg,#c9c5c6,#a8a3a5)}
.video-play{position:absolute;left:290px;top:152px;width:64px;height:64px;border-radius:50%;border:4px solid var(--white);display:flex;align-items:center;justify-content:center}
.video-note{position:absolute;left:99px;top:2140px;width:419px;height:294px;border:4px solid var(--white);background:rgba(110,45,25,.88);color:var(--white);font-size:16.5px;font-weight:600;line-height:1.55;text-align:center;padding:54px 12px 0}

/* support */
.support-title{position:absolute;left:0;width:1200px;top:2606px;text-align:center;font-family:"PT Serif",Georgia,serif;font-size:31px;font-weight:400}
.field{position:absolute;top:2677px;height:34px;border:2px solid #cfcfcf;display:flex;align-items:center;gap:8px;padding-left:22px;font-size:13px;color:#555}
.submit{position:absolute;left:988px;top:2676px;width:113px;height:36px;border-radius:18px;background:var(--teal);color:var(--white);font-family:"PT Serif",Georgia,serif;font-size:15px;display:flex;align-items:center;justify-content:center}

/* footer */
.site-footer{position:absolute;left:0;top:2807px;width:1200px;height:340px;background:var(--footer)}
.footer-brand{position:absolute;left:100px;top:70px;width:240px;text-align:center}
.footer-brand .brand-dot{width:60px;height:60px;margin:0 auto 10px}
.footer-brand .brand-name{font-size:21px}
.footer-col{position:absolute;top:52px}
.footer-col h5{font-family:"PT Serif",Georgia,serif;font-weight:400;font-size:20px;margin-bottom:22px;letter-spacing:.5px}
.footer-col li{list-style:none;font-size:13.5px;color:#555;line-height:26px;display:flex;align-items:center;gap:8px}
.footer-col .dot{width:12px;height:12px;border-radius:2px;background:#8a8a8a}
.footer-rule{position:absolute;left:99px;width:1002px;top:269px;height:1px;background:#c9c9c9}
.copyright{position:absolute;left:0;width:1200px;top:290px;text-align:center;font-size:12.5px;color:#555}
</style>
</head>
<body>

<header class="site-header">
  <div class="brand-badge"><span class="brand-dot"></span><span class="brand-name">Golden Harbor Circle</span></div>
  <nav class="main-nav">
    <a class="active" href="#">HOME</a><a href="#">ABOUT US</a><a href="#">HOW IT WORKS</a><a href="#">PRODUCTS</a><a href="#">PRICING</a><a href="#">CONTACT US</a>
  </nav>
  <div class="header-icons">
    <span><svg width="14" height="14" viewBox="0 0 14 14" fill="#fff"><circle cx="7" cy="4" r="3"/><path d="M1 14c0-4 3-6 6-6s6 2 6 6z"/></svg></span>
    <span><svg width="14" height="14" viewBox="0 0 14 14" fill="#fff"><path d="M7 13L1.5 7.5A3.2 3.2 0 0 1 7 3a3.2 3.2 0 0 1 5.5 4.5z"/></svg></span>
    <span><svg width="14" height="14" viewBox="0 0 14 14" fill="#fff"><path d="M0 1h3l2 8h7l2-6H4"/><circle cx="6" cy="12" r="1.3"/><circle cx="11" cy="12" r="1.3"/></svg></span>
  </div>
</header>

<section class="hero" role="img" aria-label="Photo of a smiling senior couple resting outdoors on a hike">
  <div class="hero-frame"></div>
  <h1>GOLDEN HARBOR CIRCLE</h1>
  <p>Sed Ut Perspiciatis Unde Omnis Iste Natus Error Sit Voluptatem Accusantium Dloremque Laudantium, Totam Rem Aperiam</p>
  <a class="btn">READ MORE</a>
  <div class="hero-arrows">
    <span><svg width="16" height="12" viewBox="0 0 16 12"><path d="M15 6H2M6 1L1 6l5 5" stroke="#fff" stroke-width="2" fill="none"/></svg></span>
    <span><svg width="16" height="12" viewBox="0 0 16 12"><path d="M1 6h13M10 1l5 5-5 5" stroke="#fff" stroke-width="2" fill="none"/></svg></span>
  </div>
</section>

<section class="welcome">
  <h2 class="welcome-title">WELCOME TO GOLDEN HARBOR CIRCLE</h2>
  <p class="welcome-text">Sed ut perspiciatis unde omnis iste natus error sit voluptatem accusantium doloremque laudantium, totam rem aperiam, eaque ipsa quae ab illo inventore veritatis et quasi architecto beatae vitae dicta sunt explicabo. Nemo enim ipsam voluptatem quia voluptas sit aspernatur aut odit aut fugit, sed quia consequuntur magni dolores eos qui ratione voluptatem nesciunt.</p>
  <div class="feature" style="left:150px;top:850px;width:210px">
    <svg width="54" height="54" viewBox="0 0 54 54" fill="var(--orange)"><circle cx="27" cy="15" r="12"/><path d="M3 54c0-15 11-24 24-24s24 9 24 24z"/></svg>
    <div style="margin-top:8px">Is It Right For Me ?</div>
  </div>
  <div class="feature-center">
    <svg width="48" height="48" viewBox="0 0 48 48" fill="none" stroke="#fff" stroke-width="4"><circle cx="24" cy="24" r="9"/><path d="M24 4v8M24 36v8M4 24h8M36 24h8M10 10l6 6M32 32l6 6M10 38l6-6M32 16l6-6"/></svg>
    <h3>How It Works ?</h3>
    <p>Various versions have evolved over the years, sometimes accident sometimes on purpose.</p>
  </div>
  <div class="feature" style="left:830px;top:850px;width:240px">
    <svg width="58" height="52" viewBox="0 0 58 52"><path d="M29 2L56 50H2z" fill="var(--orange)"/><text x="29" y="44" text-anchor="middle" fill="#fff" font-size="28" font-family="PT Serif,serif" font-weight="700">?</text></svg>
    <div style="margin-top:10px">Why Protection Needed ?</div>
  </div>
</section>

<section class="mission">
  <div class="mission-art" role="img" aria-label="Cartoon illustration of an elderly couple holding hands"></div>
  <h2>OUR MISSION</h2>
  <p>Sed ut perspiciatis unde omnis iste natus error sit voluptatem accusa ntium doloremque laudantium, totam rem aperiam, eaque ipsa quae ab illo inventore veritatis et quasi architecto beatae vitae dicta sunt explicabo. Nemo enim ipsam voluptatem quia voluptas sit aspernatur aut odit aut perspictis omnisfugit.</p>
  <a class="btn">READ MORE</a>
</section>

<section class="pricing">
  <h2 class="pricing-title">PRICING PLAN</h2>
  <div class="product-frame"><div class="product-shot" role="img" aria-label="Product photo of the wearable emergency help button pendant"></div></div>
  <svg class="product-pointer" width="26" height="22" viewBox="0 0 26 22"><path d="M0 0L26 11 0 22z" fill="var(--orange)"/></svg>

  <div class="plan" style="left:365px">
    <h4>MONTHLY</h4><div class="price">$ 20.99 <small>/ Month</small></div>
    <ul><li>✔ Sed Ut Perspiciatis Unde</li><li>✔ Omnis Iste Natus Error Sit</li><li>✔ Voluptatem Accusantium</li><li>✔ Doloremque Laudantium</li><li>✔ Totam Rem Aperiam</li></ul>
    <div class="order">ORDER NOW</div>
  </div>
  <div class="plan" style="left:623px">
    <h4>QUARTERLY</h4><div class="price">$ 30.99 <small>/ 3 Months</small></div>
    <ul><li>✔ Sed Ut Perspiciatis Unde</li><li>✔ Omnis Iste Natus Error Sit</li><li>✔ Voluptatem Accusantium</li><li>✔ Doloremque Laudantium</li><li>✔ Totam Rem Aperiam</li></ul>
    <div class="order">ORDER NOW</div>
  </div>
  <div class="plan" style="left:881px">
    <h4>SEMI-ANNUAL</h4><div class="price">$ 50.99 <small>/ 6 Months</small></div>
    <ul><li>✔ Sed Ut Perspiciatis Unde</li><li>✔ Omnis Iste Natus Error Sit</li><li>✔ Voluptatem Accusantium</li><li>✔ Doloremque Laudantium</li><li>✔ Totam Rem Aperiam</li></ul>
    <div class="order">ORDER NOW</div>
  </div>
</section>

<section class="video-band">
  <div class="video-panel" role="img" aria-label="Video still: illustration of an elderly couple at home in a living room">
    <div class="video-play"><svg width="22" height="24" viewBox="0 0 22 24"><path d="M3 1l18 11L3 23z" fill="#fff"/></svg></div>
  </div>
</section>
<div class="video-note">Sed ut perspiciatis unde omnis iste natus error sit voluptatem accusantium doloremque lau dantium, totam rem aperiam, eaque ips ae ab illo inventore veritatis et qua sihitecto beatae vitae dicta sunt quia voluptas lorem.</div>

<section class="support">
  <h2 class="support-title">SUPPORT US</h2>
  <div class="field" style="left:99px;width:411px"><svg width="11" height="11" viewBox="0 0 14 14" fill="#555"><circle cx="7" cy="4" r="3"/><path d="M1 14c0-4 3-6 6-6s6 2 6 6z"/></svg>Name</div>
  <div class="field" style="left:545px;width:414px"><svg width="13" height="10" viewBox="0 0 13 10" fill="#555"><path d="M0 0h13v10H0z"/><path d="M0 0l6.5 5L13 0" stroke="#fff" fill="none"/></svg>Email</div>
  <div class="submit">SUBMIT</div>
</section>

<footer class="site-footer">
  <div class="footer-brand"><div class="brand-dot"></div><div class="brand-name">Golden Harbor Circle</div></div>
  <div class="footer-col" style="left:459px"><h5>LINKS</h5><ul><li>Home</li><li>About Us</li><li>How It Works</li><li>Products</li><li>Pricing</li><li>Contact Us</li></ul></div>
  <div class="footer-col" style="left:711px"><h5>EXTRAS</h5><ul><li>Customer Service</li><li>Order Online</li><li>Refer a friend</li><li>Site Map</li><li>Login</li></ul></div>
  <div class="footer-col" style="left:978px"><h5>FOLLOW US</h5><ul><li><span class="dot"></span>Circlepage</li><li><span class="dot"></span>Searchly</li><li><span class="dot"></span>Workmesh</li><li><span class="dot"></span>Chirpline</li></ul></div>
  <div class="footer-rule"></div>
  <p class="copyright">Copyright © 2017, Golden Harbor Circle. All Rights Reserved.</p>
</footer>

</body>
</html>
```